Financial Services Consultant needs a business card

We need a business card for a new consulting company based in Melbourne called
"Quelbrook Insights". Tagline is Track, Review, Grow
We would like to see business card designs that are in line with the minimal style of the website www.quelbrook-insights.example
The font I have used on the website is Proxima Nova and would like the same or similar font used on the business card with a minimal design in line with the website Two sided with "QUELBROOK INSIGHTS" TRACK, REVIEW, GROW on one side and name, title and contact details on the otther
Updates

Hi All, thanks for your submissions, much appreciated.

I have recently added some colour to my webiste, it is hex #3a7b74 for those that wish to use it
Thanks

Hi all

thanks very much for your design submissions I am very impressed and they are much appreciated.

Interms of general feedback please find below;

Colour: I am trying to stick to a minimal design and colour scheme for my website which is still under construction, up to 3 colours( www.quelbrook-insights.example) it is currently black and white with a small amount of blue/green but I am open to suggestion/interpretations for a consulting company.

Card: I dont mind if it has rounded edges or straight, I was thinking about using a letterpress card if possible

Detail: the detail on the card will include; Name, Title, Mobile, Personal Email, Business Email,Web,Business Address

Once again thanks for submissions

Industry/Entity Type

Business

```html
<!DOCTYPE html>
<html lang="en">
<head>
<meta charset="utf-8">
<title>Quelbrook Insights – Business Card</title>
<link rel="stylesheet" href="https://fonts.googleapis.com/css2?family=Montserrat:wght@400;500;600;700&display=swap">
<style>
  :root {
    --bg: #ecebe8;
    --card: #ffffff;
    --ink: #141414;
    --ink-soft: #4a4a4a;
    --teal: #3a7b74;
    --on-teal: #ffffff;
    --shadow: rgba(0, 0, 0, 0.14);
  }
  * { margin: 0; padding: 0; box-sizing: border-box; }
  html, body {
    width: 1200px;
    height: 720px;
    overflow: hidden;
    background: var(--bg);
    font-family: "Montserrat", sans-serif;
    color: var(--ink);
  }
  .canvas {
    position: relative;
    width: 1200px;
    height: 720px;
    display: flex;
    align-items: center;
    justify-content: center;
    gap: 50px;
  }
  .card {
    position: relative;
    width: 540px;
    height: 310px;
    background: var(--card);
    box-shadow: 0 6px 22px var(--shadow);
  }
  .wordmark {
    font-weight: 700;
    font-size: 25px;
    letter-spacing: 0.16em;
    color: var(--ink);
    white-space: nowrap;
  }

  /* Contact side */
  .card--contact .wordmark {
    position: absolute;
    top: 56px;
    left: 0;
    right: 0;
    text-align: center;
  }
  .contact-band {
    position: absolute;
    top: 128px;
    left: 0;
    right: 0;
    height: 110px;
    background: var(--teal);
    color: var(--on-teal);
    display: flex;
    align-items: center;
    justify-content: center;
    gap: 18px;
  }
  .person { text-align: right; }
  .person__name { font-weight: 600; font-size: 17px; line-height: 1.2; }
  .person__title { font-size: 11px; font-weight: 400; opacity: 0.9; }
  .divider { width: 1px; height: 44px; background: var(--on-teal); opacity: 0.7; }
  .contact-list { list-style: none; font-size: 12px; line-height: 1.9; }
  .contact-list li { display: flex; align-items: center; gap: 7px; }
  .contact-list svg { width: 11px; height: 11px; flex: none; }
  .address {
    position: absolute;
    top: 258px;
    left: 0;
    right: 0;
    text-align: center;
    font-size: 11.5px;
    color: var(--ink-soft);
  }

  /* Brand side */
  .brand-block {
    position: absolute;
    top: 100px;
    left: 50%;
    transform: translateX(-50%);
    display: flex;
    flex-direction: column;
    align-items: flex-end;
  }
  .tagline {
    margin-top: 8px;
    font-size: 14px;
    font-weight: 400;
    color: var(--ink-soft);
    letter-spacing: 0.02em;
  }
  .brand-domain {
    margin-top: 6px;
    font-size: 12px;
    letter-spacing: 0.12em;
    color: var(--ink-soft);
  }
  .brand-domain strong { font-weight: 600; color: var(--ink); }
  .website {
    position: absolute;
    top: 244px;
    left: 0;
    right: 0;
    text-align: center;
    font-size: 14px;
    letter-spacing: 0.18em;
    color: var(--ink-soft);
  }
  .website strong { font-weight: 700; color: var(--ink); }
</style>
</head>
<body>
<main class="canvas">
  <section class="card card--contact" aria-label="Business card, contact side">
    <div class="wordmark">QUELBROOK INSIGHTS</div>
    <div class="contact-band">
      <div class="person">
        <div class="person__name">Your Name</div>
        <div class="person__title">Title</div>
      </div>
      <span class="divider" aria-hidden="true"></span>
      <ul class="contact-list">
        <li>
          <svg viewBox="0 0 12 12" aria-hidden="true"><circle cx="6" cy="6" r="5.3" fill="none" stroke="currentColor" stroke-width="1.1"/><path d="M4.2 3.3c.4-.3.8-.2 1 .2l.4.8c.1.3 0 .5-.2.7l-.3.2c.3.7.8 1.2 1.5 1.5l.2-.3c.2-.2.4-.3.7-.2l.8.4c.4.2.5.6.2 1-.4.5-1 .7-1.6.5C5.4 7.6 4.4 6.6 3.9 5.1c-.2-.6 0-1.3.3-1.8z" fill="currentColor"/></svg>
          0400-555-218
        </li>
        <li>
          <svg viewBox="0 0 12 12" aria-hidden="true"><g fill="none" stroke="currentColor" stroke-width="1"><circle cx="6" cy="6" r="5.2"/><ellipse cx="6" cy="6" rx="2.2" ry="5.2"/><path d="M0.8 6h10.4M1.6 3.4h8.8M1.6 8.6h8.8"/></g></svg>
          www.quelbrook-insights.example
        </li>
      </ul>
    </div>
    <p class="address">Street Name, City Name, State Zip Code</p>
  </section>

  <section class="card card--brand" aria-label="Business card, brand side">
    <div class="brand-block">
      <div class="wordmark">QUELBROOK INSIGHTS</div>
      <p class="tagline">Track, Review, Grow</p>
      <p class="brand-domain"><strong>quelbrook-insights</strong>.example</p>
    </div>
    <p class="website">www.<strong>quelbrook-insights</strong>.example</p>
  </section>
</main>
</body>
</html>
```